Stylish but eye catching vehicle signage for a Building and Carpentry business based in Sydney.**

We need vehicle signage for our White 2013 VW Transporter Van. We are not looking for a full wrap just signage that is eye catching, and memorable. Although we are a construction business our branding and Logo is sophisticated and clean and had a modern design . We would like to have vehicle branding that is consistent with that .

Our Logo is in grey and we would like to keep the design eye catching without using bright colours, we are not opposed to colour , we have used greys and ocre (brownish yellow)is our branding and would consider designs using these colours.

We would like to see designs that are stylish and sophisticated and not ones featuring tools or equipment for construction . We would like to see designs that portray our skills in the field of design .

Below I will attach our full logo and some examples of vehicle signage we like.
We would like the logo and contact details (email address and mobile number) on the sides and back.
We would also like the description
' new builds I renovations I residential I commercial '
at the bottom of the sides of the car between the wheels.
Updates

Hi Designers The contact details we would like on the vehicle are: 0471 839 204 rbexleybuilds@maplorn.com Just those two. Thanks

Target Market(s)

We would like to attract clients that are looking for quality work done right and professionally , and are happy to pay for good quality.

Contact Information for Business Card

I would like to go for a business card design that will accomodate embossing .
I would like the full logo on the front of the business card , no contact infomation.
The house or building icon in our logo will be raised or embossed by the printing company, so the back or the card will show the icon debossed (indented) .
On the back of the business card I would like the contact person's details:
DORIAN WEBB
carpenter
project manager
....and also the email address and mobile number on the back too.

Font styles to use
Sans Serif
Other font styles liked:
• Futura Lt Bt

Colors

Designer to choose only greyscale colors for use in the design.

Requirements
Must have
• Our logo (big and clear) and mobile number and email address on both sides and the back
Nice to have
• Designs or patterns that look architectural and elegant.
Should not have
• Any construction tools or equipment .
Designs like flames or lightning bolts
Too much colour or very bright colours

```html
<!DOCTYPE html>
<html lang="en">
<head>
<meta charset="utf-8">
<title>Bexley Builds – Business Card</title>
<link rel="stylesheet" href="https://fonts.googleapis.com/css2?family=Lato:wght@300;400;700&display=swap">
<style>
  :root {
    --backdrop: #2b2b2b;
    --card-stock: #4a4a4a;
    --deboss-ink: #3d3d3d;
    --foil: #e4e4e4;
    --foil-soft: #cfcfcf;
  }
  * { margin: 0; padding: 0; box-sizing: border-box; }
  html, body {
    width: 901px;
    height: 1200px;
    overflow: hidden;
    background: var(--backdrop);
    font-family: "Lato", sans-serif;
  }
  .sheet {
    width: 901px;
    height: 1200px;
    display: grid;
    grid-template-rows: 1fr 1fr;
  }
  .slot {
    display: flex;
    align-items: center;
    justify-content: center;
  }
  .card {
    position: relative;
    width: 600px;
    height: 340px;
    background: var(--card-stock);
    border-radius: 3px;
  }

  /* Front: debossed wordmark */
  .card--front .wordmark {
    position: absolute;
    right: 48px;
    bottom: 70px;
    display: flex;
    align-items: center;
    gap: 16px;
    color: var(--deboss-ink);
  }
  .wordmark__square {
    width: 40px;
    height: 40px;
    background: var(--deboss-ink);
  }
  .wordmark__name {
    font-weight: 300;
    font-size: 46px;
    letter-spacing: 3px;
    line-height: 1;
  }

  /* Back: foil logo + contact details */
  .card--back .wordmark {
    position: absolute;
    left: 36px;
    top: 120px;
    display: flex;
    align-items: center;
    gap: 12px;
    color: var(--foil);
  }
  .card--back .wordmark__square {
    width: 30px;
    height: 30px;
    background: var(--foil);
  }
  .card--back .wordmark__name {
    font-size: 34px;
    letter-spacing: 2px;
  }
  .contact {
    position: absolute;
    right: 40px;
    top: 150px;
    text-align: right;
    color: var(--foil);
  }
  .contact__name {
    font-weight: 700;
    font-size: 28px;
    letter-spacing: 0.5px;
    line-height: 1;
  }
  .contact__role {
    font-weight: 400;
    font-size: 17px;
    color: var(--foil-soft);
    margin-top: 2px;
  }
  .contact__phone {
    font-weight: 700;
    font-size: 25px;
    margin-top: 22px;
    text-align: left;
  }
  .contact__email {
    font-weight: 400;
    font-size: 16px;
    margin-top: 4px;
    text-align: left;
  }
</style>
</head>
<body>
  <main class="sheet">
    <section class="slot">
      <div class="card card--front">
        <div class="wordmark">
          <span class="wordmark__square"></span>
          <span class="wordmark__name">BEXLEY BUILDS</span>
        </div>
      </div>
    </section>
    <section class="slot">
      <div class="card card--back">
        <div class="wordmark">
          <span class="wordmark__square"></span>
          <span class="wordmark__name">BEXLEY BUILDS</span>
        </div>
        <div class="contact">
          <p class="contact__name">DORIAN WEBB</p>
          <p class="contact__role">Carpenter</p>
          <p class="contact__phone">Call:0471 839 204</p>
          <p class="contact__email">rbexleybuilds@maplorn.com</p>
        </div>
      </div>
    </section>
  </main>
</body>
</html>
```